Health and Fitness Club requires a stunning and simple website

We are a health and fitness club based in Dubai, when we launch we will be the biggest club in the country, we will also have the 2 largest activity rooms in the country, we are setting a new standard in the industry by offering one thing, our attitude.

Our attitude means the following:
unlike other clubs we have no hidden charges or fees
our members can join daily, monthly, 6 months or annually
our service and facility are comparable to 5* hotel gyms
our equipment is second to none
our space is the biggest in the country
we do not force our members to use our in-house personal trainers - you can bring your own and we will not charge them entry!
we will have a cutting edge brawnmesh box in our gym with classes by the best trainers in the country
we will be providing free-lance personal trainers a platform to engage customers, grow their business and even use our activity rooms for classes

Basically we will be a gym like no other, simply because we are gym people and we hate the restrictive practices and hidden charges by other gyms, so we are making our own gym which focuses on quality and service.

All of this has to be communicated in the style of the website, the colors of the website we want to be limited to the logo colors as this will be the same theme running throughout the gym.

The landing page of the website HAS to incorporate elements from our social media presences, this basically is the usual, chirplo, snapvault, kinwall. We can have these as a sidebar, the centre of the page should display the latest article from our blog (also on the website) Also we need to have a calendar for activities and classes on the front page. The menu should have links to the following:
Latest News
About us
Team
Gallery
Membership
Classes
Member Log In
Contact Us
Location

The style of the website has to be similar to the logo, particularly in terms of the fonts used.

```html
<!DOCTYPE html>
<html lang="en">
<head>
<meta charset="utf-8">
<title>Ironroom Health &amp; Fitness Club</title>
<link href="https://fonts.googleapis.com/css2?family=Cabin:wght@400;500&family=Arimo:wght@400;700&display=swap" rel="stylesheet">
<style>
:root{
  --red:#a50d12;
  --red-bright:#e0433a;
  --ink:#222;
  --text:#333;
  --muted:#666;
  --nav-top:#3a3a3a;
  --nav-bottom:#111;
  --line:#e6e6e6;
  --panel:#f7f7f7;
  --caption:#4a4a4a;
  --footer:#333;
  --white:#fff;
}
*{box-sizing:border-box;margin:0;padding:0}
html,body{width:938px;height:1200px;overflow:hidden;background:var(--white)}
body{position:relative;font-family:"Arimo",Arial,sans-serif;color:var(--text)}
.site-header{position:absolute;left:0;top:0;width:938px;height:110px}
.brand{position:absolute;left:78px;top:14px;display:flex;align-items:center;gap:8px}
.brand-mark{width:22px;height:22px;border-radius:50%;background:var(--red)}
.brand-name{font-family:"Cabin",sans-serif;font-size:22px;font-weight:500;color:var(--ink);line-height:72px}
.contact{position:absolute;right:78px;top:42px;display:flex;gap:20px;font-size:9.5px;color:var(--ink);align-items:center}
.contact-item{display:flex;align-items:center;gap:10px}
.contact-icon{width:24px;height:24px;border-radius:50%;background:#555;display:flex;align-items:center;justify-content:center}
.main-nav{position:absolute;left:0;top:110px;width:938px;height:36px;background:linear-gradient(var(--nav-top),var(--nav-bottom))}
.main-nav ul{list-style:none;display:flex;margin-left:78px;height:36px}
.main-nav li{font-size:11px;color:var(--white);padding:0 15px;line-height:36px}
.main-nav li.active{background:var(--red);padding:0 18px}
.hero{position:absolute;left:0;top:146px;width:938px;height:362px;background:linear-gradient(100deg,#d9d4cc 0%,#8a8580 40%,#6a6e78 60%,#a9b4c4 85%,#dde3ea 100%);box-shadow:0 6px 10px rgba(0,0,0,.12)}
.hero-title{position:absolute;left:78px;top:119px;width:431px;height:60px;background:var(--caption);color:var(--white);font-family:"Cabin",sans-serif;font-size:30px;font-weight:500;line-height:60px;padding-left:17px}
.hero-sub{position:absolute;left:78px;top:179px;width:466px;height:39px;background:rgba(245,245,245,.95);color:var(--caption);font-family:"Cabin",sans-serif;font-size:12.5px;line-height:39px;padding-left:17px}
.hero-arrow{position:absolute;top:183px;width:18px;height:26px;background:rgba(255,255,255,.6);display:flex;align-items:center;justify-content:center}
.hero-arrow.prev{left:0}.hero-arrow.next{right:0}
.hero-dots{position:absolute;left:422px;top:341px;width:98px;height:16px;background:rgba(255,255,255,.7);border-radius:4px 4px 0 0;display:flex;justify-content:center;align-items:center;gap:5px}
.hero-dots span{width:9px;height:9px;border-radius:50%;background:#888}
.hero-dots span.on{background:var(--red)}
.col-title{position:absolute;top:538px;font-family:"Cabin",sans-serif;font-size:19px;color:var(--ink);letter-spacing:.5px}
.card{position:absolute;top:571px;width:249px;height:304px;border:1px solid var(--line)}
.card-media{margin:2px;height:142px;position:relative}
.card-date{position:absolute;left:0;bottom:0;background:var(--caption);color:var(--white);font-family:"Cabin",sans-serif;font-size:14px;padding:0 10px;line-height:40px}
.card-title{font-family:"Cabin",sans-serif;font-size:15px;color:var(--ink);margin:14px 0 0 15px}
.card-text{font-size:8.8px;line-height:17px;color:var(--ink);margin:9px 14px 0 15px}
.btn-red{position:absolute;left:17px;top:263px;width:65px;height:26px;background:var(--red);color:var(--white);font-size:10.5px;line-height:26px;text-align:center;border-radius:2px}
.promo{position:absolute;left:78px;top:909px;width:517px;height:181px;background:var(--panel)}
.promo-media{position:absolute;left:0;top:0;width:194px;height:181px;background:linear-gradient(90deg,#3a3a3a,#b8b2aa 45%,#c23a3a 60%,#4a4a4a)}
.promo-body{position:absolute;left:216px;top:18px;width:290px}
.promo-title{font-family:"Cabin",sans-serif;font-size:20px;color:var(--ink);letter-spacing:.3px}
.promo-offer{font-family:"Cabin",sans-serif;font-size:9.5px;color:var(--red);margin-top:12px;letter-spacing:.3px}
.promo-text{font-size:9px;line-height:17px;color:var(--ink);margin-top:12px}
.btn-dark{display:inline-block;margin-top:17px;width:87px;height:29px;background:#555;color:var(--white);font-family:"Cabin",sans-serif;font-size:11px;line-height:29px;text-align:center;border-radius:2px}
.calendar{position:absolute;left:613px;top:907px;width:248px;height:184px;border:1px solid var(--line)}
.cal-caption{font-size:9px;text-align:center;line-height:24px;color:var(--ink)}
.calendar table{width:100%;border-collapse:collapse;font-size:8.5px;text-align:center}
.calendar th{background:#2e2e2e;color:var(--white);height:22px;font-weight:700}
.calendar td{height:22.4px;border:1px solid #eee;color:var(--muted)}
.calendar td.today{background:var(--red);color:var(--white);font-weight:700}
.calendar td.nav{font-weight:700;color:var(--text)}
.site-footer{position:absolute;left:0;top:1116px;width:938px;height:84px;background:var(--footer)}
.copyright{position:absolute;left:78px;top:36px;font-size:9px;color:#ddd}
.social{position:absolute;right:78px;top:32px;display:flex;gap:14px;list-style:none}
.social li{display:flex;align-items:center;gap:5px;font-family:"Arimo",sans-serif;font-size:10.5px;color:var(--red-bright);line-height:20px}
.social li::before{content:"";width:12px;height:12px;border-radius:50%;background:var(--red-bright)}
</style>
</head>
<body>
<header class="site-header">
  <div class="brand"><span class="brand-mark"></span><span class="brand-name">Ironroom</span></div>
  <div class="contact">
    <div class="contact-item"><span class="contact-icon"><svg width="12" height="12" viewBox="0 0 24 24"><path fill="#fff" d="M6.6 10.8a15 15 0 006.6 6.6l2.2-2.2a1 1 0 011-.25 11.4 11.4 0 003.6.6 1 1 0 011 1V20a1 1 0 01-1 1A17 17 0 013 4a1 1 0 011-1h3.5a1 1 0 011 1 11.4 11.4 0 00.6 3.6 1 1 0 01-.25 1z"/></svg></span>Call Us : +47 40012345</div>
    <div class="contact-item"><span class="contact-icon"><svg width="12" height="12" viewBox="0 0 24 24"><rect x="3" y="6" width="18" height="12" fill="#fff"/><path d="M3 6l9 7 9-7" stroke="#555" stroke-width="1.6" fill="none"/></svg></span>hello@ironroomclub.no</div>
  </div>
</header>

<nav class="main-nav">
  <ul>
    <li class="active">Home</li><li>About us</li><li>Team</li><li>Gallery</li><li>Membership</li><li>Classes</li><li>Member Log In</li><li>Contact Us</li><li>Location</li>
  </ul>
</nav>

<section class="hero" role="img" aria-label="Photo of smiling club members stretching together on exercise mats">
  <div class="hero-title">Build some online muscle</div>
  <div class="hero-sub">Whip your Gym or Fitness centre in shape with the theme that can do it all.</div>
  <div class="hero-arrow prev"><svg width="8" height="12" viewBox="0 0 8 12"><path d="M6 1L1 6l5 5" stroke="#fff" stroke-width="2" fill="none"/></svg></div>
  <div class="hero-arrow next"><svg width="8" height="12" viewBox="0 0 8 12"><path d="M2 1l5 5-5 5" stroke="#fff" stroke-width="2" fill="none"/></svg></div>
  <div class="hero-dots"><span></span><span></span><span class="on"></span><span></span><span></span><span></span></div>
</section>

<h2 class="col-title" style="left:78px">Our Trainers</h2>
<h2 class="col-title" style="left:345px">Recent News</h2>
<h2 class="col-title" style="left:612px">Our Classes</h2>

<article class="card" style="left:78px">
  <div class="card-media" role="img" aria-label="Black and white photo of a trainer coaching a woman lifting a dumbbell" style="background:linear-gradient(90deg,#3c3c3c,#cfcfcf 50%,#555 80%,#e0e0e0)"></div>
  <h3 class="card-title">Running for fitness</h3>
  <p class="card-text">Excepteur sint occaecat cupidatat non proident, sunt in culpa qui officia deserunt mollit anim id, consecte-tur, adipisci velit, sed quia non numquam eius modi tempora incidunt.</p>
  <span class="btn-red">More Info</span>
</article>

<article class="card" style="left:345px">
  <div class="card-media" role="img" aria-label="Photo of many hands holding soil with a young green plant" style="background:linear-gradient(160deg,#6a4a3a,#b07a5a 45%,#3a2a22 75%,#5a6a88)">
    <span class="card-date">Feb 02</span>
  </div>
  <h3 class="card-title">Looking Beyond Common</h3>
  <p class="card-text">Excepteur sint occaecat cupidatat non proident, sunt in culpa qui officia deserunt mollit anim id, consecte-tur, adipisci velit, sed quia non numquam eius modi tempora incidunt.</p>
  <span class="btn-red">More Info</span>
</article>

<article class="card" style="left:612px">
  <div class="card-media" role="img" aria-label="Photo of a physiotherapist assisting a man on a leg exercise machine" style="background:linear-gradient(90deg,#e8ecef,#f4f4f4 40%,#c8ccd2 70%,#8a8e96)"></div>
  <h3 class="card-title">Weight room blunders</h3>
  <p class="card-text">Excepteur sint occaecat cupidatat non proident, sunt in culpa qui officia deserunt mollit anim id, consecte-tur, adipisci velit, sed quia non numquam eius modi tempora incidunt.</p>
  <span class="btn-red">More Info</span>
</article>

<section class="promo">
  <div class="promo-media" role="img" aria-label="Photo of a man in a red vest lifting a barbell"></div>
  <div class="promo-body">
    <h2 class="promo-title">BALANCE - FITNESS FOR LIFE</h2>
    <p class="promo-offer">ZERO DOWN - ONLY $19.99 A MONTH FOR 3 MONTHS</p>
    <p class="promo-text">Lorem ipsum dolor sit amet consect adipisscin elit proin vel lectus ut eta esami vera dolor sit amet</p>
    <span class="btn-dark">Get Started</span>
  </div>
</section>

<section class="calendar">
  <div class="cal-caption">February 2014</div>
  <table>
    <thead><tr><th>M</th><th>T</th><th>W</th><th>T</th><th>F</th><th>S</th><th>S</th></tr></thead>
    <tbody>
      <tr><td></td><td></td><td></td><td></td><td></td><td>1</td><td>2</td></tr>
      <tr><td>3</td><td>4</td><td>5</td><td>6</td><td>7</td><td>8</td><td>9</td></tr>
      <tr><td>10</td><td>11</td><td>12</td><td>13</td><td>14</td><td>15</td><td>16</td></tr>
      <tr><td>17</td><td>18</td><td class="today">19</td><td>20</td><td>21</td><td>22</td><td>23</td></tr>
      <tr><td>24</td><td>25</td><td>26</td><td>27</td><td>28</td><td></td><td></td></tr>
      <tr><td colspan="3" class="nav">« Oct</td><td></td><td colspan="3"></td></tr>
    </tbody>
  </table>
</section>

<footer class="site-footer">
  <p class="copyright">© 2014 health &amp; fitness club. All rights reserved.</p>
  <ul class="social">
    <li>kinwall</li><li>chirplo</li><li>wavecast</li><li>tumblo</li><li>vidmo</li><li>pinlane</li><li>snapvault</li>
  </ul>
</footer>
</body>
</html>
```